Create a memorable Web Design for real estate branding

we are a Minnepolis brokerage and boutique housing specialist with over 27 years of experience in the Global furnished housing industry, servicing the Greater Los Angeles area. Specializing in “warm environments” we offer a customized approach to satisfying our guests and client’s needs by offering a wide array of options in highly desirable areas. Additionally, Lantern Dwelling Partners offers assistance and expertise to home buyers, sellers and investors.

Industry/Entity Type

Real Estate

Number of Pages Required

1 page

Font styles to use
Serif
Sans Serif
Decorative

```html
<!DOCTYPE html>
<html lang="en">
<head>
<meta charset="utf-8">
<title>Lantern Dwelling Partners</title>
<link rel="stylesheet" href="https://fonts.googleapis.com/css2?family=Cinzel:wght@400;700&family=Raleway:wght@400;500;600;700&family=Open+Sans:wght@400;600&display=swap">
<style>
:root{
  --teal:#10a88e;
  --teal-dark:#0b8f78;
  --green:#7dc243;
  --green-light:#8fd14f;
  --ink:#2b2b2b;
  --text:#444;
  --muted:#777;
  --line:#ddd;
  --panel:#f1f1f1;
  --dark:#262a2c;
  --night:#1f2b30;
}
*{box-sizing:border-box;margin:0;padding:0}
html,body{width:1200px;height:2687px;overflow:hidden}
body{position:relative;font-family:"Open Sans",Arial,sans-serif;color:var(--text);background:#fff}
.abs{position:absolute}

/* hero */
.hero{position:absolute;left:0;top:0;width:1200px;height:614px;background:linear-gradient(180deg,#6d5a43 0%,#a58a64 35%,#8a6b4a 60%,#4e3a28 100%)}
.hero-window{position:absolute;left:300px;top:150px;width:420px;height:260px;background:linear-gradient(180deg,#c9d6dc,#7f9a82);opacity:.75}
.topbar{position:absolute;left:0;top:0;width:1200px;height:129px;background:rgba(20,20,20,.72)}
.logo{position:absolute;left:104px;top:38px;font-family:"Raleway",sans-serif;font-weight:700;color:var(--green-light);font-size:30px;line-height:34px}
.logo small{display:block;font-size:24px;padding-left:70px}
.consult{position:absolute;left:815px;top:0;width:267px;height:34px;background:var(--teal);border:2px solid #7fd6c2;color:#fff;font-family:"Cinzel",serif;font-size:15px;text-align:center;line-height:30px}
.contact-top{position:absolute;top:52px;color:#fff;font-size:14px;display:flex;align-items:center;gap:8px}
.contact-top.phone{font-size:19px}
.nav{position:absolute;left:432px;top:90px;display:flex;font-family:"Cinzel",serif;font-size:15px;color:#fff}
.nav a{padding:0 15px;border-right:1px solid #888;text-decoration:none;color:#fff}
.nav a:first-child{padding-left:0;color:var(--green-light)}
.nav a:last-child{border:0}
.slide-arrow{position:absolute;top:344px;width:34px;height:28px;background:#333;display:flex;align-items:center;justify-content:center}
.tabs{position:absolute;left:104px;top:426px;display:flex}
.tabs span{height:30px;line-height:30px;padding:0 16px;font-size:15px;background:var(--green);color:#111;margin-right:2px;font-family:"Raleway",sans-serif}
.tabs span:first-child{background:var(--teal);color:#fff}
.search-panel{position:absolute;left:104px;top:456px;width:661px;height:154px;background:rgba(40,40,40,.75);border-radius:0 0 6px 6px}
.search-input{position:absolute;left:14px;top:24px;width:522px;height:36px;background:#fff;font-size:13px;padding:10px 12px;color:#333}
.search-btn{position:absolute;left:544px;top:24px;width:90px;height:36px;background:#4d4d4d;color:#fff;font-size:14px;text-align:center;line-height:36px}
.field-label{position:absolute;top:76px;color:#fff;font-size:12px}
.select{position:absolute;top:102px;width:147px;height:30px;background:#fff;font-size:12px;padding:7px 10px;color:#333}
.select::after{content:"";position:absolute;right:10px;top:12px;border:6px solid transparent;border-top-color:var(--green)}

/* about */
.about-photo{position:absolute;left:102px;top:660px;width:235px;height:270px;background:linear-gradient(160deg,#dfe6ea,#7f8d97 60%,#2d3338)}
.h2{font-family:"Raleway",sans-serif;font-weight:500;color:var(--ink);font-size:22px}
.rule{position:absolute;height:2px;background:var(--line)}
.rule i{position:absolute;left:0;top:0;height:2px;width:50px;background:var(--green)}
.about-copy{position:absolute;left:352px;top:700px;width:444px;font-size:13.5px;line-height:21px;color:#555}
.ticks{position:absolute;left:352px;top:772px;width:380px;list-style:none;font-size:12px;line-height:17px;color:#444}
.ticks li{position:relative;padding-left:24px;margin-bottom:8px}
.ticks svg{position:absolute;left:0;top:2px}
.btn-teal{position:absolute;background:var(--teal);color:#fff;text-align:center;font-size:12px}
.offer{position:absolute;left:796px;width:310px}
.offer .ico{position:absolute;left:0;top:0;width:40px;height:40px;border:1px solid #bbb;display:flex;align-items:center;justify-content:center}
.offer h4{margin-left:56px;font-size:13px;font-weight:600;color:#222}
.offer p{margin-left:56px;font-size:11.5px;line-height:17px;color:#555}

/* featured */
.featured{position:absolute;left:0;top:978px;width:1200px;height:277px;background:linear-gradient(180deg,#3a4246,#2b3236 60%,#4a5258)}
.featured-title{position:absolute;left:0;top:1016px;width:1200px;text-align:center;color:#fff;font-family:"Raleway",sans-serif;font-size:22px}
.card{position:absolute;top:1112px;width:226px;height:303px;background:#fff;border:1px solid #ccc}
.card .pic{position:absolute;left:8px;top:8px;width:208px;height:128px}
.card h5{position:absolute;left:8px;top:150px;font-size:14px;font-weight:400;color:#222}
.card .sub{position:absolute;left:8px;top:176px;font-size:12px;color:#777}
.badge{position:absolute;left:8px;top:220px;height:26px;line-height:26px;padding:0 10px;font-size:12px;color:#fff}
.price{position:absolute;right:10px;top:214px;font-size:22px;color:#2b9ed8}
.stats{position:absolute;left:0;bottom:0;width:100%;height:40px;border-top:1px solid var(--line);display:flex}
.stats span{flex:1;border-right:1px solid var(--line);font-size:10px;color:#777;display:flex;align-items:center;justify-content:center;gap:4px}
.stats span:last-child{border:0}

/* cta band */
.cta{position:absolute;left:0;top:1466px;width:1200px;height:80px;background:var(--teal)}
.cta p{position:absolute;left:112px;top:14px;width:760px;color:#fff;font-size:18px;line-height:26px}
.cta-call{position:absolute;left:903px;top:12px;width:192px;height:57px;background:#333;border-radius:4px;color:#fff;text-align:center;font-size:14px;padding-top:6px}
.cta-call b{display:block;font-size:22px;font-weight:400}

/* looking for */
.look-title{position:absolute;left:0;top:1606px;width:1200px;text-align:center}
.look-img{position:absolute;top:1688px;width:386px;height:257px}
.look-h{position:absolute;top:1958px;width:476px;text-align:center;font-family:"Raleway",sans-serif;font-size:17px;font-weight:500;color:#222}
.look-p{position:absolute;top:1988px;width:476px;text-align:center;font-size:13px;line-height:21px;color:#444}

/* forms */
.refer{position:absolute;left:0;top:2080px;width:578px;height:202px;background:var(--panel)}
.news{position:absolute;left:594px;top:2080px;width:606px;height:202px;background:var(--panel)}
.form-h{position:absolute;font-family:"Raleway",sans-serif;font-size:22px;font-weight:500;color:#222}
.input{position:absolute;height:40px;background:#fff;border:1px solid #ccc;font-size:12px;padding:12px 10px;color:#444}

/* footer */
.footer{position:absolute;left:0;top:2282px;width:1200px;height:363px;background:linear-gradient(180deg,#1d2529,#2a3338 50%,#1c2326)}
.foot-h{position:absolute;top:2358px;font-family:"Cinzel",serif;font-size:18px;color:#fff}
.foot-h em{font-style:normal;color:var(--green)}
.quick{position:absolute;left:104px;top:2410px;list-style:none;color:#fff;font-size:12px}
.quick li{height:38px}
.quick li::before{content:"›";margin-right:10px}
.fc{position:absolute;left:312px;color:#fff;font-size:13px;line-height:19px}
.fc .sq{position:absolute;left:0;top:0;width:28px;height:28px;background:var(--green);display:flex;align-items:center;justify-content:center}
.fc div{margin-left:40px}
.social{position:absolute;left:624px;color:#fff;font-size:11px;display:flex;align-items:center;gap:14px;letter-spacing:.5px}
.social i{width:36px;height:36px;border-radius:50%;display:block}
.foot-logo{position:absolute;left:825px;top:2430px;font-family:"Raleway",sans-serif;font-weight:700;color:var(--green-light);font-size:34px;line-height:38px;text-align:right}
.copy{position:absolute;left:0;top:2645px;width:1200px;height:42px;background:var(--teal);color:#fff;font-size:13px;text-align:center;line-height:42px}
</style>
</head>
<body>

<!-- Hero -->
<section class="hero" role="img" aria-label="Photo of a furnished apartment living room with sofas and a balcony view"></section>
<div class="hero-window"></div>
<header class="topbar">
  <div class="logo">Lantern Dwelling<small>Partners</small></div>
  <div class="consult">Schedule Free Consultation</div>
  <div class="contact-top" style="left:710px">
    <svg width="16" height="12" viewBox="0 0 16 12"><rect width="16" height="12" fill="#7dc243"/><path d="M0 0l8 7 8-7" stroke="#fff" fill="none"/></svg>
    info@lanterndwelling.com
  </div>
  <div class="contact-top phone" style="left:945px">
    <svg width="20" height="20" viewBox="0 0 20 20"><circle cx="10" cy="10" r="9" fill="none" stroke="#7dc243" stroke-width="2"/><path d="M7 5l2 3-1 1 3 3 1-1 3 2-2 2c-4 0-8-4-8-8z" fill="#7dc243"/></svg>
    123-456-7890
  </div>
  <nav class="nav"><a>Find a Home</a><a>Sell Your Home</a><a>Lantern Blog</a><a>Our Agents</a><a>Contact Us</a></nav>
</header>
<div class="slide-arrow" style="left:0"><svg width="10" height="12"><path d="M8 1L2 6l6 5" stroke="#fff" stroke-width="2" fill="none"/></svg></div>
<div class="slide-arrow" style="right:0"><svg width="10" height="12"><path d="M2 1l6 5-6 5" stroke="#fff" stroke-width="2" fill="none"/></svg></div>

<div class="tabs"><span>For Sale</span><span>To Rent</span><span>Developments</span><span>Map Search</span></div>
<div class="search-panel">
  <div class="search-input">Find property for sale in Minneapolis</div>
  <div class="search-btn">SEARCH</div>
  <div class="field-label" style="left:14px">Property Type</div>
  <div class="field-label" style="left:171px">Price Range</div>
  <div class="field-label" style="left:486px">Beds</div>
  <div class="select" style="left:14px">Any</div>
  <div class="select" style="left:171px">For Any</div>
  <div class="select" style="left:330px">To Any</div>
  <div class="select" style="left:486px">Any</div>
</div>

<!-- About -->
<div class="about-photo" role="img" aria-label="Photo of a smiling agent in a suit meeting a client at a desk"></div>
<div class="h2 abs" style="left:352px;top:654px">About Lantern Dwelling Partners</div>
<div class="rule" style="left:352px;top:688px;width:348px"><i></i></div>
<p class="about-copy">Lorem ipsum dolor sit amet, consectetuer adipiscing elit, sed diam nonummy nibh euismod tincidunt ut laoreet dore magna aliquam erat volutpat. Ut wisi enim ad minim.</p>
<ul class="ticks">
  <li><svg width="14" height="14"><circle cx="7" cy="7" r="6" fill="none" stroke="#7dc243" stroke-width="1.5"/><path d="M4 7l2 2 4-4" stroke="#7dc243" stroke-width="1.5" fill="none"/></svg>we are a Minnepolis brokerage and boutique housing specialist with over 27 years of experience</li>
  <li><svg width="14" height="14"><circle cx="7" cy="7" r="6" fill="none" stroke="#7dc243" stroke-width="1.5"/><path d="M4 7l2 2 4-4" stroke="#7dc243" stroke-width="1.5" fill="none"/></svg>Specializing in "warm environments"</li>
  <li><svg width="14" height="14"><circle cx="7" cy="7" r="6" fill="none" stroke="#7dc243" stroke-width="1.5"/><path d="M4 7l2 2 4-4" stroke="#7dc243" stroke-width="1.5" fill="none"/></svg>we offer a customized approach to satisfying our guests and client's needs by offering a wide array of options in highly desirable areas</li>
</ul>
<div class="btn-teal" style="left:352px;top:897px;width:103px;height:36px;line-height:36px">READ MORE</div>

<div class="h2 abs" style="left:796px;top:654px;font-size:20px">Offers Assistance &amp; Expertise To</div>
<div class="rule" style="left:796px;top:688px;width:302px"><i></i></div>
<div class="offer" style="top:712px"><div class="ico"><svg width="24" height="24"><rect x="2" y="2" width="20" height="20" fill="none" stroke="#7dc243" stroke-width="2"/><circle cx="12" cy="12" r="4" fill="#7dc243"/></svg></div><h4>Buyers</h4><p>Lorem ipsum dolor sit amet, consectetuer adipiscing elit, sed dianonummy nibh</p></div>
<div class="offer" style="top:794px"><div class="ico"><svg width="24" height="24"><path d="M2 14l6-6 4 3 4-3 6 6-10 6z" fill="#7dc243"/></svg></div><h4>Sellers</h4><p>Lorem ipsum dolor sit amet, consectetuer adipiscing elit, sed dianonum</p></div>
<div class="offer" style="top:876px"><div class="ico"><svg width="24" height="24"><circle cx="10" cy="8" r="5" fill="#7dc243"/><path d="M2 22c0-6 4-9 8-9s8 3 8 9z" fill="#7dc243"/></svg></div><h4>Investors</h4><p>Lorem ipsum dolor sit amet, consectetuer adi elit, sed dianonummy nibh euismod</p></div>

<!-- Featured -->
<section class="featured" role="img" aria-label="Dimmed photo of a city skyline"></section>
<div class="featured-title">Featured Property Listings</div>
<div class="rule" style="left:404px;top:1060px;width:392px;background:#aaa"><i style="left:171px"></i></div>

<div class="card" style="left:104px">
  <div class="pic" role="img" aria-label="Photo of a large stone house" style="background:linear-gradient(180deg,#9cc0e0,#cfc7b8 55%,#6f8a4e)"></div>
  <h5>123 Dollar Smit Amet</h5><div class="sub">Duis autem vel eum iriure</div>
  <div class="badge" style="background:var(--teal)">For Rent</div><div class="price">$ 123</div>
  <div class="stats"><span>▫ 1200 sq ft</span><span>▭ 2 Beds</span><span>◦ 2 Baths</span></div>
</div>
<div class="card" style="left:360px">
  <div class="pic" role="img" aria-label="Photo of a modern interior with a red wall" style="background:linear-gradient(135deg,#e8e8ec,#b0b6c0 50%,#c23a2c 70%,#6b6f76)"></div>
  <h5>123 Dollar Smit Amet</h5><div class="sub">Duis autem vel eum iriure</div>
  <div class="badge" style="background:#333">Sold</div><div class="price">$ 213</div>
  <div class="stats"><span>▫ 1200 sq ft</span><span>▭ 2 Beds</span><span>◦ 2 Baths</span></div>
</div>
<div class="card" style="left:614px">
  <div class="pic" role="img" aria-label="Photo of a bright living room with blue sofas" style="background:linear-gradient(160deg,#d8e4ee,#8aa6c2 55%,#8c7b64)"></div>
  <h5>123 Dollar Smit Amet</h5><div class="sub">Duis autem vel eum iriure</div>
  <div class="badge" style="background:#333">For Rent</div><div class="price">$ 143</div>
  <div class="stats"><span>▫ 1200 sq ft</span><span>▭ 2 Beds</span><span>◦ 2 Baths</span></div>
</div>
<div class="card" style="left:870px">
  <div class="pic" role="img" aria-label="Photo of a dark grey two-storey house" style="background:linear-gradient(180deg,#c7dbe9,#4c5560 50%,#3f5a34)"></div>
  <h5>123 Dollar Smit Amet</h5><div class="sub">Duis autem vel eum iriure</div>
  <div class="badge" style="background:#333">For Sell</div><div class="price">$ 132</div>
  <div class="stats"><span>▫ 1200 sq ft</span><span>▭ 2 Beds</span><span>◦ 2 Baths</span></div>
</div>

<!-- CTA -->
<section class="cta">
  <p>Sed ut perspiciatis unde omnis iste natus error sit Accusant doloremque lorems ispum monis laudantium, totamrem aperiam, moregi eaquemn.</p>
  <div class="cta-call">Call Us Today<b>123-456-7890</b></div>
</section>

<!-- Looking for -->
<div class="look-title h2">What Are You Looking For</div>
<div class="rule" style="left:404px;top:1640px;width:392px"><i style="left:160px;width:70px"></i></div>
<div class="look-img" style="left:164px;background:linear-gradient(180deg,#d88a3c,#c9c2b6 40%,#7a6a58)" role="img" aria-label="Photo of a modern lounge interior with round ceiling panels"></div>
<div class="look-img" style="left:652px;background:linear-gradient(180deg,#b9cfe0,#9aa7a8 45%,#5d7a44)" role="img" aria-label="Photo of a couple shaking hands with an agent outside a house"></div>
<div class="look-h" style="left:119px">BUYING A PROPERTY</div>
<div class="look-h" style="left:607px">SELLING A PROPERTY</div>
<p class="look-p" style="left:119px">Lorem ipsum dolor sit amet, consectetuer adipiscing elit, sed diam nonummy nibh euismod tincidunt ut laoreet dolore magna aliquam erat volutpat. Ut wisi enim ad minim veniam,</p>
<p class="look-p" style="left:607px">Lorem ipsum dolor sit amet, consectetuer adipiscing elit, sed diam nonummy nibh euismod tincidunt ut laoreet dolore magna aliquam erat volutpat. Ut wisi enim ad minim veniam,</p>

<!-- Refer & newsletter -->
<section class="refer"></section>
<section class="news"></section>
<svg class="abs" style="left:104px;top:2096px" width="36" height="34" viewBox="0 0 36 34"><rect x="1" y="8" width="24" height="24" fill="none" stroke="#7dc243" stroke-width="3"/><path d="M10 22c0-8 6-12 14-12V4l10 9-10 9v-6c-6 0-10 2-14 6z" fill="#7dc243"/></svg>
<div class="form-h" style="left:150px;top:2100px">Refer A Friend</div>
<div class="input" style="left:104px;top:2145px;width:212px">From*</div>
<div class="input" style="left:332px;top:2145px;width:213px">To*</div>
<div class="input" style="left:104px;top:2195px;width:361px">Message (Optional)</div>
<div class="btn-teal" style="left:465px;top:2195px;width:80px;height:40px;line-height:40px;font-size:19px">Send</div>
<div class="abs" style="left:110px;top:2243px;font-size:11px;color:#444">*Privacy Policy</div>

<svg class="abs" style="left:620px;top:2096px" width="52" height="40" viewBox="0 0 52 40"><path d="M2 16L26 2l24 14v22H2z" fill="#7dc243"/><path d="M2 16l24 14 24-14" stroke="#fff" stroke-width="2" fill="none"/><rect x="12" y="8" width="28" height="14" fill="#fff"/></svg>
<div class="form-h" style="left:684px;top:2100px">Join Our newsletter for exclusive deals</div>
<p class="abs" style="left:620px;top:2150px;width:490px;font-size:11.5px;line-height:18px;color:#333">Lorem ut wisi enim ad minim veniam, quis nostrm ci tation ullamcorper suscipit lobol ritis nisl ut aliquip ex ea ad commo.</p>
<div class="input" style="left:620px;top:2212px;width:195px;height:44px">Email Address</div>
<div class="btn-teal" style="left:815px;top:2210px;width:132px;height:48px;line-height:48px;font-size:19px">Subscribe</div>

<!-- Footer -->
<footer class="footer" role="img" aria-label="Dimmed photo of a city skyline at dusk"></footer>
<div class="foot-h" style="left:104px">Quick <em>Links</em></div>
<ul class="quick"><li>Find A Home</li><li>Sell Your Home</li><li>Lantern Blog</li><li>Our Agents</li><li>Contact Us</li></ul>

<div class="foot-h" style="left:312px">Contact <em>Details</em></div>
<div class="fc" style="top:2406px"><span class="sq"><svg width="14" height="18"><path d="M7 1a6 6 0 0 1 6 6c0 5-6 10-6 10S1 12 1 7a6 6 0 0 1 6-6z" fill="#fff"/><circle cx="7" cy="7" r="2" fill="#7dc243"/></svg></span><div><b style="font-weight:600">Office:</b><br>123, Lorem ipsum dolor<br>sit amet, consecte 32145</div></div>
<div class="fc" style="top:2488px"><span class="sq"><svg width="16" height="16"><path d="M3 1l3 4-2 2 5 5 2-2 4 3-2 2C7 15 1 9 1 3z" fill="#fff"/></svg></span><div style="line-height:28px">123 456 7890</div></div>
<div class="fc" style="top:2550px"><span class="sq"><svg width="16" height="12"><rect width="16" height="12" fill="#fff"/><path d="M0 0l8 7 8-7" stroke="#7dc243" fill="none"/></svg></span><div style="line-height:28px">info@lanterndwelling.com</div></div>

<div class="foot-h" style="left:624px">Follow <em style="color:#fff">Us</em></div>
<div class="social" style="top:2404px"><i style="background:#3b5998"></i>FRIENDBOOK</div>
<div class="social" style="top:2454px"><i style="background:#1da1f2"></i>CHIRPER</div>
<div class="social" style="top:2504px"><i style="background:#0e76a8"></i>WORKLINK</div>
<div class="social" style="top:2554px"><i style="background:#d34836"></i>CIRCLE PLUS</div>

<div class="foot-logo">Lantern Dwelling<br>Partners</div>

<div class="copy">Copyright © 2016 Lantern Dwelling Partners. All rights reserved.</div>
</body>
</html>
```